Veterinary Pylon

My veterinary clinic is not clearly visible from the street and I want to place a Pylon next to my driveway. I want a modern, elegant straight Design, the Photo shows the sheduled place. One can see the clinic on our Homepage: www.tailbright-vethaus.at
The last pictures are examples for pylones I like

Target Market(s)

the passing cars often miss my entry...I want to show where to turn left

Colors
3276b5
33a6d7
00a990

Requirements
Must have
• High value, simple elegance, size: 250cm (high) x 100cm (width)
Nice to have
• Our Logo, arrow(?)

A special Text is not necessary but this will be an option:

Biegen sie hier ab und wir biegen es wieder hin!
Should not have
• Too much Color, the colors I have chosen are the possible colors but it‘s not necessary to use them.

```html
<!DOCTYPE html>
<html lang="de">
<head>
<meta charset="utf-8">
<title>Tailbright Vethaus – Pylon</title>
<link rel="stylesheet" href="https://fonts.googleapis.com/css2?family=Montserrat:wght@400;500;600;700&display=swap">
<style>
  :root {
    --navy: #29488a;
    --sky: #40b8dd;
    --white: #ffffff;
    --backdrop: #eef1f4;
  }
  * { margin: 0; padding: 0; box-sizing: border-box; }
  html, body {
    width: 818px;
    height: 1200px;
    overflow: hidden;
    background: var(--backdrop);
    font-family: "Montserrat", sans-serif;
  }
  .canvas {
    position: relative;
    width: 818px;
    height: 1200px;
  }
  .pylon-panels {
    position: absolute;
    left: 0;
    top: 0;
  }
  .brand-plate {
    position: absolute;
    left: 122px;
    top: 332px;
    width: 454px;
    height: 165px;
    background: var(--white);
    padding: 10px;
  }
  .brand-plate__frame {
    width: 100%;
    height: 100%;
    border: 2px solid var(--navy);
    display: flex;
    align-items: center;
    justify-content: center;
    gap: 18px;
  }
  .brand-mark {
    width: 46px;
    height: 46px;
    border-radius: 50%;
    background: var(--sky);
    flex: none;
  }
  .brand-name {
    color: var(--navy);
    font-weight: 700;
    font-size: 34px;
    line-height: 1.05;
    letter-spacing: 0.01em;
  }
  .headline {
    position: absolute;
    left: 332px;
    top: 544px;
    width: 290px;
    color: var(--white);
    font-weight: 600;
    font-size: 30.5px;
    line-height: 35.5px;
  }
  .hours {
    position: absolute;
    left: 333px;
    width: 240px;
    border-left: 1.5px solid var(--white);
    padding-left: 9px;
    color: var(--white);
    font-size: 16.5px;
    line-height: 21px;
  }
  .hours--weekdays { top: 695px; }
  .hours--saturday { top: 777px; }
  .hours--sunday { top: 856px; }
  .hours__day {
    color: var(--sky);
    font-weight: 600;
    letter-spacing: 0.02em;
    text-transform: uppercase;
    margin-top: 2px;
  }
  .hours__time { font-weight: 500; }
  .web-bar {
    position: absolute;
    left: 333px;
    top: 942px;
    width: 363px;
    height: 48px;
    background: var(--white);
    display: flex;
    align-items: center;
    justify-content: center;
    color: var(--navy);
    font-weight: 600;
    font-size: 18px;
  }
</style>
</head>
<body>
  <div class="canvas">
    <svg class="pylon-panels" width="818" height="1200" viewBox="0 0 818 1200" aria-hidden="true">
      <polygon class="panel-back" points="353,229 696,85 696,1115 353,1115" fill="var(--sky)"/>
      <rect class="panel-front" x="284" y="296" width="333" height="819" fill="var(--navy)"/>
    </svg>

    <div class="brand-plate">
      <div class="brand-plate__frame">
        <span class="brand-mark"></span>
        <span class="brand-name">Tailbright<br>Vethaus</span>
      </div>
    </div>

    <p class="headline">Biegen Sie ein,<br>dann biegen wir<br>es hin!</p>

    <div class="hours hours--weekdays">
      <p class="hours__day">Monday - Friday</p>
      <p class="hours__time">08:00 - 12:00</p>
      <p class="hours__time">14:00 - 19:00</p>
    </div>
    <div class="hours hours--saturday">
      <p class="hours__day">Saturday</p>
      <p class="hours__time">08:00 - 12:00</p>
      <p class="hours__time">17:00 - 18:00</p>
    </div>
    <div class="hours hours--sunday">
      <p class="hours__day">Sunday</p>
      <p class="hours__time">10:00 am - 11:00 am</p>
      <p class="hours__time">17:00 - 18:00</p>
    </div>

    <div class="web-bar">www.tailbright-vethaus.at</div>
  </div>
</body>
</html>
```